Corporate Branded Documents - IT Provider - On-going work

Hi, I'm Ned a Director of Harbourlane ICT Support a UK Based IT & Telecoms support firm. We've been trading for 12 years now and feel its time for a lick of paint. We have a logo, website etc but would like someone to create some standard documents for us.

- A PDF Proposal Template - We currently don't send our customers proposals as we have nothing that looks good.
- A Quote Template PDF - Example Attached
- A Order Template PDF - Example Attached
- A Invoice Template PDF - Example Attached
- A Generic Document PDF - Something we can use for customer application forms, NDA Agreements, Terms & Conditions etc

Our website can be found at www.harbourlaneictsupport.co.uk - here you'll get a feel for our branding. I've also attached 2 example documents - as well as our currently used documents. Hopefully you guys can see why it needs improving.

We'd also like to work with someone long term, these documents are a start but we'd like to make sure all the work we do looks and feels as smart as possible, so there is plenty of additional work available.

None of these templates need to be Print ready, 99% of the time it will be viewed digitally, so high resolution designs are best

Thanks,

Ned

Target Market(s)

Corporate & Educational Customers

Industry/Entity Type

It Support

Font styles to use
Sans Serif

Colors
ec1f27
0692cd
ffffff

```html
<!DOCTYPE html>
<html lang="en">
<head>
<meta charset="utf-8">
<title>Harbourlane ICT Support – Document Page</title>
<link href="https://fonts.googleapis.com/css2?family=Carlito:wght@400;700&display=swap" rel="stylesheet">
<style>
  :root {
    --heading-teal: #0e7a93;
    --text-body: #3f3f3f;
    --row-tint: #e9f2f6;
    --row-plain: #f6f6f6;
    --page-bg: #ffffff;
    --footer-rule: #9a9a9a;
    --header-text: #ffffff;
  }
  * { box-sizing: border-box; margin: 0; padding: 0; }
  html, body { width: 851px; height: 1200px; overflow: hidden; background: var(--page-bg); }
  body {
    position: relative;
    font-family: "Carlito", "Calibri", sans-serif;
    color: var(--text-body);
  }
  .company-name {
    position: absolute;
    top: 22px;
    right: 30px;
    font-size: 22px;
    font-weight: 400;
    color: var(--text-body);
    line-height: 1;
  }
  .subtitle {
    position: absolute;
    top: 112px;
    left: 30px;
    font-size: 33px;
    font-weight: 700;
    color: var(--heading-teal);
  }
  .body-text {
    position: absolute;
    left: 30px;
    width: 789px;
    font-size: 19.3px;
    line-height: 31.8px;
    text-align: justify;
  }
  .intro { top: 154px; }
  .closing { top: 942px; }
  .price-table {
    position: absolute;
    top: 389px;
    left: 30px;
    width: 789px;
    border-collapse: collapse;
    font-size: 20px;
  }
  .price-table th {
    background: var(--heading-teal);
    color: var(--header-text);
    font-weight: 700;
    font-size: 19.5px;
    height: 43px;
    text-align: left;
    padding-left: 15px;
  }
  .price-table td {
    height: 60px;
    padding-left: 15px;
    border-bottom: 1px solid var(--page-bg);
  }
  .price-table tbody tr:nth-child(odd) td { background: var(--row-tint); }
  .price-table tbody tr:nth-child(even) td { background: var(--row-plain); }
  .price-table .col-a { width: 311px; }
  .price-table .col-b { width: 340px; }
  .price-table .col-price { text-align: right; padding-right: 38px; }
  .price-table th.col-price { padding-right: 30px; }
  .page-footer {
    position: absolute;
    top: 1152px;
    right: 30px;
    display: flex;
    align-items: center;
    font-size: 19px;
    height: 36px;
  }
  .footer-label { padding-right: 10px; }
  .footer-rule { width: 1px; height: 36px; background: var(--footer-rule); }
  .page-number { padding-left: 10px; font-weight: 700; font-size: 21px; }
</style>
</head>
<body>
  <header class="company-name">Harbourlane ICT Support</header>

  <h2 class="subtitle">Subtitle Here</h2>

  <p class="body-text intro">Lorem Ipsum is simply dummy text of the printing and typesetting industry. Lorem Ipsum has been the industry's industry. Lorem Ipsum has been the finishLorem Ipsum is simply dummy text of the printing and typesetting industry. Lorem Ipsum has been the industry's industry. Lorem Ipsum has been the finishLorem Ipsum is simply dummy text of the printing and typesetting industry. Lorem Ipsum has been the industry's industry. Lorem Ipsum has been the finishLorem Ipsum is simply dummy text of the printing and typesetting industry. Lorem Ipsum has been the industry's industry. Lorem Ipsum has been the finish.</p>

  <table class="price-table">
    <thead>
      <tr>
        <th class="col-a">Table Section Title Here</th>
        <th class="col-b">Table Section Title Here</th>
        <th class="col-price">Title Here</th>
      </tr>
    </thead>
    <tbody>
      <tr><td>Table Section subtext here</td><td>Table Section subtext here</td><td class="col-price">$150.00</td></tr>
      <tr><td>Table Section subtext here</td><td>Table Section subtext here</td><td class="col-price">$150.00</td></tr>
      <tr><td>Table Section subtext here</td><td>Table Section subtext here</td><td class="col-price">$150.00</td></tr>
      <tr><td>Table Section subtext here</td><td>Table Section subtext here</td><td class="col-price">$150.00</td></tr>
      <tr><td>Table Section subtext here</td><td>Table Section subtext here</td><td class="col-price">$150.00</td></tr>
      <tr><td>Table Section subtext here</td><td>Table Section subtext here</td><td class="col-price">$150.00</td></tr>
      <tr><td>Table Section subtext here</td><td>Table Section subtext here</td><td class="col-price">$150.00</td></tr>
      <tr><td>Table Section subtext here</td><td>Table Section subtext here</td><td class="col-price">$150.00</td></tr>
    </tbody>
  </table>

  <p class="body-text closing">Lorem Ipsum is simply dummy text of the printing and typesetting industry. Lorem Ipsum has been the industry's industry. Lorem Ipsum has been the finishLorem Ipsum is simply dummy text of the printing and typesetting industry. Lorem Ipsum has been the industry's industry. Lorem Ipsum has been the finishLorem Ipsum is simply dummy text<br>&nbsp;of the printing and typesetting industry. Lorem Ipsum has been the industry's industry.</p>

  <footer class="page-footer">
    <span class="footer-label">Confendtial</span>
    <span class="footer-rule"></span>
    <span class="page-number">2</span>
  </footer>
</body>
</html>
```